Vantiqo custom business card design

Need a authentic, innovative business card design for a new mobile app business. I am uploading a few screen images from our app for you to view. I would like app design theme to match business card design. I can also send logo images.

```html
<!DOCTYPE html>
<html lang="en">
<head>
<meta charset="UTF-8">
<title>Vantiqo Business Card</title>
<link href="https://fonts.googleapis.com/css2?family=Montserrat:wght@700;800&family=Lato:wght@400;700&display=swap" rel="stylesheet">
<style>
  :root {
    --backdrop: #9b9b9b;
    --card-white: #ffffff;
    --brand-purple: #5f008f;
    --ink: #1b1b1b;
    --rule: #e2e2e2;
  }
  html, body {
    margin: 0;
    padding: 0;
    width: 1200px;
    height: 900px;
    overflow: hidden;
    background: var(--backdrop);
  }
  .canvas {
    position: relative;
    width: 1200px;
    height: 900px;
  }
  .card {
    position: absolute;
    top: 274px;
    width: 477px;
    height: 294px;
    box-sizing: border-box;
  }
  .card-front {
    left: 120px;
    background: var(--card-white);
    border-radius: 0 48px 0 48px;
  }
  .card-back {
    left: 607px;
    background: var(--brand-purple);
    border-radius: 48px 0 48px 0;
    display: flex;
    align-items: center;
    justify-content: center;
    gap: 14px;
  }
  .brand-block {
    position: absolute;
    left: 52px;
    top: 78px;
    width: 146px;
    display: flex;
    flex-direction: column;
    align-items: center;
  }
  .brand-dot {
    width: 92px;
    height: 92px;
    border-radius: 50%;
    background: var(--brand-purple);
  }
  .brand-name {
    margin-top: 16px;
    font-family: "Montserrat", sans-serif;
    font-weight: 800;
    font-size: 31px;
    line-height: 1;
    color: var(--ink);
  }
  .divider {
    position: absolute;
    left: 222px;
    top: 74px;
    width: 1px;
    height: 146px;
    background: var(--rule);
  }
  .contact-block {
    position: absolute;
    left: 245px;
    top: 73px;
    font-family: "Lato", sans-serif;
    color: var(--ink);
  }
  .person-name {
    margin: 0;
    font-family: "Montserrat", sans-serif;
    font-weight: 700;
    font-size: 16px;
    line-height: 20px;
    color: var(--brand-purple);
  }
  .person-role {
    margin: 0 0 5px;
    font-size: 13.5px;
    line-height: 17px;
  }
  .contact-list {
    list-style: none;
    margin: 0;
    padding: 0;
    font-size: 13.5px;
    line-height: 17.5px;
  }
  .contact-list li {
    display: flex;
    align-items: center;
    gap: 4px;
  }
  .contact-list svg {
    width: 10px;
    height: 10px;
    fill: var(--brand-purple);
    flex: none;
  }
  .address {
    margin: 7px 0 0;
    font-size: 13.5px;
    line-height: 17.5px;
  }
  .back-dot {
    width: 40px;
    height: 40px;
    border-radius: 50%;
    background: var(--card-white);
  }
  .back-name {
    font-family: "Montserrat", sans-serif;
    font-weight: 800;
    font-size: 40px;
    color: var(--card-white);
  }
</style>
</head>
<body>
<main class="canvas">
  <section class="card card-front">
    <div class="brand-block">
      <div class="brand-dot"></div>
      <div class="brand-name">Vantiqo</div>
    </div>
    <div class="divider"></div>
    <div class="contact-block">
      <h1 class="person-name">DANIEL MORROW</h1>
      <p class="person-role">Managing Director</p>
      <ul class="contact-list">
        <li><svg viewBox="0 0 10 10"><path d="M1 3.5C1 2 3 1.5 5 1.5S9 2 9 3.5V4.5H7V3.6H3V4.5H1Z M2 5.5H8L9 9H1Z"/></svg>044-987 654 321</li>
        <li><svg viewBox="0 0 10 10"><path d="M2.5 0.5H7.5V9.5H2.5Z M3.3 1.5V7.8H6.7V1.5Z"/></svg>044-987 654 321</li>
        <li><svg viewBox="0 0 10 10"><path d="M0.5 2H9.5V8H0.5Z" /><path d="M0.8 2.3L5 5.5L9.2 2.3" fill="none" stroke="#fff" stroke-width="0.9"/></svg>hello@vantiqo.com</li>
        <li><svg viewBox="0 0 10 10"><circle cx="5" cy="5" r="4.5"/></svg>www.vantiqo.com</li>
      </ul>
      <p class="address">12345, Address Goes Here<br>Country Name, 123456.</p>
    </div>
  </section>
  <section class="card card-back">
    <div class="back-dot"></div>
    <div class="back-name">Vantiqo</div>
  </section>
</main>
</body>
</html>
```